App Design Project

Hello,
I'm looking for a great designer for my iOS Applications, we have a lot of works and we're short in designers :(
I want to revamp my thermometer iOS app. You will find attached the images I want to replace. I need something with the same element (temp, condition, weather icon) but with a different look!
Same, new icon, you have carte blanche to this one.
I want a design that stands out from the hundreds of weather application that almost all the same design. I am looking for something that does say "wow, it rocks."
Please do not Provide classic design that we can see everywhere ... I'm looking for something with a real artistic choice, contrast, colours, etc.
As a marketing screenshot, I want something classic, you'll find an example attached, feel free to innovate.
To sum-up :
- One new view for my App
- One new icon
- One marketing screenshot
Marketing

```html
<!DOCTYPE html>
<html lang="en">
<head>
<meta charset="utf-8">
<title>Weather App – Current Conditions</title>
<link href="https://fonts.googleapis.com/css2?family=Raleway:wght@200&family=Poppins:wght@600&family=Roboto:wght@400&family=Libre+Baskerville:ital,wght@1,700&display=swap" rel="stylesheet">
<style>
  :root {
    --canvas-bg: #e3e3e3;
    --sky-top: #4e3550;
    --sky-mid: #c88c9c;
    --sky-low: #a77488;
    --sky-bottom: #5e4263;
    --paper: #ffffff;
    --paper-fold: #ececec;
    --paper-shade: #dcdcdc;
    --paper-veil: rgba(255, 255, 255, 0.32);
    --ink: #1c1c1e;
    --ink-soft: #2b2226;
    --title-light: #f5ecf1;
  }
  html, body {
    margin: 0;
    width: 1200px;
    height: 1200px;
    overflow: hidden;
    background: var(--canvas-bg);
  }
  .app-screen {
    position: absolute;
    left: 300px;
    top: 71px;
    width: 600px;
    height: 1058px;
    display: block;
  }
  .condition-title {
    font-family: "Raleway", sans-serif;
    font-weight: 200;
    font-size: 48px;
    fill: var(--title-light);
    text-anchor: middle;
  }
  .condition-detail {
    font-family: "Roboto", sans-serif;
    font-weight: 400;
    font-size: 17px;
    fill: var(--ink-soft);
    text-anchor: middle;
  }
  .temp-celsius,
  .temp-unit,
  .temp-fahrenheit {
    font-family: "Poppins", sans-serif;
    font-weight: 600;
    fill: var(--ink);
  }
  .temp-celsius { font-size: 150px; letter-spacing: -2px; }
  .temp-unit { font-size: 100px; }
  .temp-fahrenheit { font-size: 62px; letter-spacing: 1px; }
  .info-button {
    font-family: "Libre Baskerville", serif;
    font-style: italic;
    font-weight: 700;
    font-size: 34px;
    fill: var(--ink);
  }
</style>
</head>
<body>
<svg class="app-screen" viewBox="0 0 432 762" xmlns="http://www.w3.org/2000/svg">
  <defs>
    <linearGradient id="sky" x1="0" y1="0" x2="0" y2="1">
      <stop offset="0" stop-color="var(--sky-top)"/>
      <stop offset="0.25" stop-color="var(--sky-mid)"/>
      <stop offset="0.6" stop-color="var(--sky-low)"/>
      <stop offset="1" stop-color="var(--sky-bottom)"/>
    </linearGradient>
  </defs>

  <g class="sky-backdrop" role="img" aria-label="Stormy pink and purple sky with lightning">
    <rect width="432" height="762" fill="url(#sky)"/>
  </g>

  <g class="paper-panel">
    <rect x="298" y="0" width="134" height="276" fill="var(--paper)"/>
    <polygon points="298,276 432,150 432,276" fill="var(--paper-fold)"/>
    <polygon points="298,140 298,276 380,200" fill="var(--paper-shade)" opacity="0.5"/>
  </g>

  <g class="paper-band">
    <rect x="0" y="276" width="432" height="135" fill="var(--paper)"/>
    <polygon points="0,276 70,312 0,350" fill="var(--paper-fold)"/>
    <polygon points="0,411 140,360 300,411" fill="var(--paper-fold)" opacity="0.7"/>
    <polygon points="300,411 432,330 432,411" fill="var(--paper-shade)" opacity="0.6"/>
  </g>

  <polygon class="paper-veil" points="0,441 216,596 432,441" fill="var(--paper-veil)"/>
  <line class="divider" x1="0" y1="439" x2="370" y2="439" stroke="var(--ink)" stroke-width="1"/>

  <text class="condition-title" x="148" y="110">THUNDER</text>
  <text class="condition-title" x="148" y="172">STORMS</text>
  <text class="condition-detail" x="148" y="222">HUMIDITY: 87%</text>
  <text class="condition-detail" x="148" y="248">N/NW AT 8 MPH</text>

  <text class="temp-celsius" x="48" y="398">28</text>
  <circle class="temp-degree" cx="241" cy="290" r="8" fill="none" stroke="var(--ink)" stroke-width="4"/>
  <text class="temp-unit" x="258" y="361">C</text>

  <text class="temp-fahrenheit" x="52" y="516">82.4 °F</text>

  <path class="refresh-icon" d="M376 432 A12 12 0 1 1 370 446" fill="none" stroke="var(--ink)" stroke-width="3.5"/>
  <polygon points="368,430 382,428 376,440" fill="var(--ink)"/>

  <text class="info-button" x="370" y="740">i</text>
</svg>
</body>
</html>
```